Creative Web Design for an ERP (technology) Consulting Business

I need two pages designed for the ERP Project Management Consulting Company I am starting. One page is the home page, the other page is an important inside page.

I've looked at many different templates for sites like this, and they all look the same to me. I am working with PixelGuild designers because I want something unique.

This site will be implemented with Wordpress using the Elementor framework,

About Me ---
I have worked with PixelGuild several times before, and I have tired to do everything I can to ve helpful. In the uploads, you will find PDF's with wireframes outlning the layout of the pages, as well as explanatios for each section. There are Word documents that you can copy into text. The list below explains the files included.

Although the wireframes suggest a layout, please feel free to use your creativity - often, I find that the designs I like the most are designs I have never thought of.

About the Company --
ERP (Enterprise Resource Planning) systems are business computer systems that tie different businesss functions together. These systems are expensive and complicated, and efforts to implement them often fail. The purpose of the company is to increase the chance of success by focusing on the things that need to be right.

I have uploaded several files to help clarify what I am looking for:
• 1a - Home Page Wireframe - PDF
Wireframe for the home page with an explanation of each section.
• 1b - Home Page Text – Word
A Word document so that you can copy the text.
• 2 - Copper Harbor Logo – ZIP
Four different versions of the company logo in Adobe Illustrator, PNG, and JPG formats. Any of the four are acceptable:
1. Logo_1 – Black on Transparent – Same Line ERP
2. Logo_2 – White on Transparent – Same Line ERP
3. Logo_3 – Black on Transparent – Big ERP on Different Line
4. Logo_4 – White on Transparent – Big ERP on Different Line
• 3a - Copper Harbor Page Wireframe – PDF
Wireframe for he Copper Harbor page, with explanations and a detailed breakdown of the top section.
• 3b - Copper Harbor Text – Word
• 4 - Colors and Palettes – PDF
• 5 - Change Management Icon – EPS
• 6 – Site Map
If you wish to see it, the site map provides an idea of the entire site. The two pages circled in red are the ones I need to be designed.

Thank you for your interest in this project!

Target Market(s)

Corporate decision makers, primarily CIOs and CFOs, as well as ERP project managers and influencers.

Industry/Entity Type

Consulting

Number of Pages Required

2 page

Font styles to use
Sans Serif

Requirements
Must have
• Pages that contain the elements explained on the wireframes provided.
Nice to have
• A design that looks and feels unique
Should not have
• A typical, template layour

```html
<!DOCTYPE html>
<html lang="en">
<head>
<meta charset="utf-8">
<title>Copper Harbor — Eight &amp; Adaptive 8 Method</title>
<link href="https://fonts.googleapis.com/css2?family=Inter:wght@400;500;600;700&display=swap" rel="stylesheet">
<style>
:root{
  --bg:#efefef;
  --ink:#141414;
  --muted:#5a5a5a;
  --white:#ffffff;
  --black:#0d0d0d;
  --copper:#e07b5b;
  --lavender:#dcd5ec;
  --slate:#62676b;
  --plum:#6e5d9b;
  --fog:#d5d8de;
  --periwinkle:#a9abd3;
  --line:#e3e3e3;
}
*{box-sizing:border-box;margin:0;padding:0}
html,body{width:673px;height:1200px;overflow:hidden}
body{background:var(--bg);font-family:"Inter",sans-serif;color:var(--ink);position:relative}
.abs{position:absolute}

/* header */
.brand{left:12px;top:12px;display:flex;align-items:center;gap:6px;font-weight:700;font-size:14px;color:var(--ink)}
.brand-dot{width:26px;height:26px;border-radius:50%;background:var(--copper)}
.nav{left:213px;top:21px;display:flex;gap:40px;font-size:10.5px;font-weight:500;letter-spacing:.3px}
.search{left:541px;top:20px}
.talk{left:571px;top:6px;width:102px;height:42px;border-radius:21px;background:var(--black);color:var(--white);font-size:11px;display:flex;align-items:center;justify-content:center}

/* hero */
.eyebrow{font-size:8px;letter-spacing:1px;color:#9a9a9a;text-transform:uppercase}
.hero-eyebrow{left:20px;top:104px}
.hero-title{left:20px;top:120px;font-size:37px;line-height:44px;font-weight:600;letter-spacing:-1px;width:360px}
.hero-text{left:20px;top:227px;width:280px;font-size:14px;line-height:19px;color:#2a2a2a}
.btn-light{left:18px;top:296px;width:136px;height:42px;border-radius:21px;background:var(--white);font-size:13px;font-weight:600;display:flex;align-items:center;justify-content:center;gap:8px;box-shadow:0 1px 3px rgba(0,0,0,.05)}
.network{left:356px;top:108px;width:300px;height:228px;border-radius:16px;background:radial-gradient(circle at 35% 30%,#f3c9ae 0%,transparent 45%),radial-gradient(circle at 75% 70%,#c4b5e2 0%,transparent 50%),linear-gradient(135deg,#ebe3ea,#e2ddee)}

/* feature row */
.video-card{left:10px;top:384px;width:320px;height:198px;border-radius:12px;background:linear-gradient(135deg,#e08a68,#c96a4d 60%,#b45a42);color:var(--white);overflow:hidden}
.video-card p{position:absolute;left:15px;top:18px;width:295px;font-size:13.5px;line-height:21px;font-weight:500}
.video-art{position:absolute;left:100px;top:95px;width:140px;height:95px;border-radius:50% 50% 8px 8px;background:radial-gradient(circle at 50% 40%,#e9a588,#b85c42 70%)}
.progress{position:absolute;left:17px;top:168px;width:292px;height:2px;background:rgba(255,255,255,.9)}
.time{position:absolute;top:156px;font-size:7px;opacity:.85}
.controls{position:absolute;left:17px;top:176px;font-size:7px;opacity:.85}

.services-card{left:342px;top:384px;width:322px;height:198px;border-radius:12px;background:var(--white)}
.services-card h2{position:absolute;left:14px;top:18px;font-size:17px;font-weight:400}
.services-card .rule{position:absolute;left:14px;right:14px;top:58px;height:1px;background:var(--line)}
.service{position:absolute;width:140px}
.service h3{font-size:10.5px;font-weight:600;margin-bottom:4px}
.service p{font-size:9px;line-height:13px;color:var(--muted)}
.divider-v{position:absolute;left:165px;top:64px;width:1px;height:120px;background:var(--line)}
.divider-h{position:absolute;left:14px;right:14px;top:129px;height:1px;background:var(--line)}

/* services section */
.sec-eyebrow{left:0;width:673px;top:639px;text-align:center}
.sec-title{left:0;width:673px;top:656px;text-align:center;font-size:37px;font-weight:600;letter-spacing:-1px}
.btn-dark{left:267px;top:719px;width:140px;height:41px;border-radius:21px;background:var(--black);color:var(--white);font-size:11.5px;display:flex;align-items:center;justify-content:center}

.tile{width:155px;height:178px;border-radius:11px;overflow:hidden}
.tile .fav{position:absolute;right:12px;top:14px}
.tile .icon{position:absolute;left:17px;top:60px}
.tile h4{position:absolute;left:17px;top:107px;font-size:15px;font-weight:600;letter-spacing:-.3px}
.tile p{position:absolute;left:17px;top:133px;width:125px;font-size:9px;line-height:12px}
.t-lavender{background:var(--lavender);color:var(--ink)}
.t-slate{background:var(--slate);color:var(--white)}
.t-plum{background:var(--plum);color:var(--white)}
.t-copper{background:var(--copper);color:var(--white)}
.t-fog{background:var(--fog);color:var(--ink)}
.t-peri{background:var(--periwinkle);color:var(--white)}
.t-photo{background:linear-gradient(180deg,#a9a49c,#6e6760 55%,#8a6f58)}
</style>
</head>
<body>

<header>
  <div class="abs brand"><span class="brand-dot"></span>Copper Harbor</div>
  <nav class="abs nav"><span>HOME</span><span>COMPANY</span><span>PORTAL</span><span>CONTACT</span></nav>
  <svg class="abs search" width="12" height="12" viewBox="0 0 12 12" fill="none" stroke="#111" stroke-width="1.5"><circle cx="5" cy="5" r="3.8"/><path d="M8 8l3 3"/></svg>
  <a class="abs talk">Let's Talk</a>
</header>

<section class="hero">
  <div class="abs eyebrow hero-eyebrow">ERP Framework</div>
  <h1 class="abs hero-title">Eight &amp; Adaptive 8 Method.</h1>
  <p class="abs hero-text">A framework grouping critical factors into high level categories for ERP project success.</p>
  <a class="abs btn-light">Learn More <span>→</span></a>
  <div class="abs network" role="img" aria-label="Illustration of six linked icon nodes forming the Adaptive 8 network"></div>
</section>

<section class="feature-row">
  <div class="abs video-card">
    <p>Adaptive 8 Method blends waterfall planning and agile execution for every ERP project.</p>
    <div class="video-art" role="img" aria-label="Illustration of a consulting workspace"></div>
    <span class="time" style="left:17px">0:00</span>
    <span class="time" style="left:298px">3:28</span>
    <div class="progress"></div>
    <span class="controls">0:00 ◂ ▸</span>
  </div>

  <div class="abs services-card">
    <h2>Services sections</h2>
    <div class="rule"></div>
    <div class="divider-v"></div>
    <div class="divider-h"></div>
    <div class="service" style="left:14px;top:72px"><h3>Project Planning</h3><p>Building a solid roadmap for launch.</p></div>
    <div class="service" style="left:177px;top:72px"><h3>Project Staffing</h3><p>Resourcing and onboarding teams.</p></div>
    <div class="service" style="left:14px;top:141px"><h3>Project Oversight and QA</h3><p>Independent quality reviews.</p></div>
    <div class="service" style="left:177px;top:141px"><h3>Client Matching</h3><p>Selecting the right partners.</p></div>
  </div>
</section>

<section class="services">
  <div class="abs eyebrow sec-eyebrow">Services</div>
  <h2 class="abs sec-title">Services Section</h2>
  <a class="abs btn-dark">Explore Services</a>

  <div class="abs tile t-lavender" style="left:10px;top:802px">
    <svg class="fav" width="10" height="10" viewBox="0 0 10 10" fill="none" stroke="currentColor"><circle cx="5" cy="5" r="4"/></svg>
    <svg class="icon" width="22" height="20" viewBox="0 0 22 20" fill="none" stroke="#4a3f70" stroke-width="1.2"><rect x="2" y="3" width="18" height="14"/><path d="M6 7h10M6 11h6"/></svg>
    <h4>ERP Fit &amp; Gap</h4><p>Needs assessment and vendor shortlist.</p>
  </div>
  <div class="abs tile t-slate" style="left:176px;top:802px">
    <svg class="fav" width="10" height="10" viewBox="0 0 10 10" fill="none" stroke="currentColor"><circle cx="5" cy="5" r="4"/></svg>
    <svg class="icon" width="26" height="20" viewBox="0 0 26 20" fill="none" stroke="#fff" stroke-width="1.2"><rect x="2" y="2" width="22" height="16" rx="2"/><path d="M2 7h22M6 11h8"/></svg>
    <h4>Workflow</h4><p>Process design and change support.</p>
  </div>
  <div class="abs tile t-photo" style="left:342px;top:802px" role="img" aria-label="Photo of a consultant working in a bright office"></div>
  <div class="abs tile t-plum" style="left:508px;top:802px">
    <svg class="fav" width="10" height="10" viewBox="0 0 10 10" fill="none" stroke="currentColor"><circle cx="5" cy="5" r="4"/></svg>
    <svg class="icon" width="22" height="20" viewBox="0 0 22 20" fill="none" stroke="#fff" stroke-width="1.2"><rect x="3" y="4" width="16" height="13"/><path d="M7 4V1h8v3M7 9h8"/></svg>
    <h4>Strategy</h4><p>Roadmaps tailored to your goals.</p>
  </div>

  <div class="abs tile t-plum" style="left:10px;top:992px">
    <svg class="fav" width="10" height="10" viewBox="0 0 10 10" fill="none" stroke="currentColor"><circle cx="5" cy="5" r="4"/></svg>
    <svg class="icon" width="22" height="20" viewBox="0 0 22 20" fill="none" stroke="#fff" stroke-width="1.2"><rect x="2" y="2" width="18" height="16" rx="2"/><path d="M6 7h10M6 11h10"/></svg>
    <h4>Methodology</h4><p>Proven steps for smooth rollouts.</p>
  </div>
  <div class="abs tile t-copper" style="left:176px;top:992px">
    <svg class="fav" width="10" height="10" viewBox="0 0 10 10" fill="none" stroke="currentColor"><circle cx="5" cy="5" r="4"/></svg>
    <svg class="icon" width="22" height="20" viewBox="0 0 22 20" fill="none" stroke="#fff" stroke-width="1.2"><rect x="3" y="3" width="16" height="14"/><path d="M7 13l4-5 4 5"/></svg>
    <h4>Client Matching</h4><p>Finding the right fit for teams.</p>
  </div>
  <div class="abs tile t-fog" style="left:342px;top:992px">
    <svg class="fav" width="10" height="10" viewBox="0 0 10 10" fill="none" stroke="currentColor"><circle cx="5" cy="5" r="4"/></svg>
    <svg class="icon" width="26" height="20" viewBox="0 0 26 20" fill="none" stroke="#333" stroke-width="1.2"><circle cx="9" cy="12" r="6"/><circle cx="18" cy="8" r="6"/></svg>
    <h4>Sourcing</h4><p>Independent vendor selection and negotiation.</p>
  </div>
  <div class="abs tile t-peri" style="left:508px;top:992px">
    <svg class="fav" width="10" height="10" viewBox="0 0 10 10" fill="none" stroke="currentColor"><circle cx="5" cy="5" r="4"/></svg>
    <svg class="icon" width="26" height="20" viewBox="0 0 26 20" fill="none" stroke="#fff" stroke-width="1.2"><rect x="2" y="4" width="22" height="12" rx="2"/><path d="M2 8h22"/></svg>
    <h4>Change Scaling</h4><p>Preparing teams for new systems.</p>
  </div>
</section>

</body>
</html>
```